Need Web Design for Business Process Outsourcing Company (Quorvane)

Quorvane is a business process outsourcing company. Need a simple site similar to http://www.tallowbrinkhire.com/ but with a more professional and credible look. New to the process; not sure where to start and comparing my options. Please let me know what my options are if I choose to go with you. Logo is attached for your reference. Please use same colorway

Reason: I want the final product to be coded. Please confirm you will be able to code final design.

Industry/Entity Type

Business

Coding

Coded - Design and coding required

```html
<!DOCTYPE html>
<html lang="en">
<head>
<meta charset="utf-8">
<title>Quorvane Services</title>
<link href="https://fonts.googleapis.com/css2?family=Lato:wght@400;700&family=Open+Sans:wght@400;600;700&family=Roboto:wght@400;500&display=swap" rel="stylesheet">
<style>
:root{
  --navy:#0d4f86;
  --navy-deep:#0a3d6b;
  --accent:#1a8acb;
  --accent-bright:#2196d6;
  --ink:#222;
  --muted:#555;
  --grey-band:#ebebeb;
  --white:#fff;
}
*{box-sizing:border-box;margin:0;padding:0}
html,body{width:1200px;height:2643px;overflow:hidden}
body{position:relative;font-family:'Roboto',sans-serif;color:var(--ink);background:var(--white)}
.abs{position:absolute}

/* Hero */
.hero{left:0;top:0;width:1200px;height:660px;background:linear-gradient(160deg,#1d4f80 0%,#2a6aa0 40%,#174a7c 70%,#0e3c6a 100%)}
.brand{left:99px;top:26px;display:flex;align-items:center;gap:14px;color:var(--white);font-family:'Open Sans',sans-serif;font-weight:700;font-size:40px;letter-spacing:.5px}
.brand-mark{width:52px;height:52px;border:4px solid var(--white);border-radius:6px}
.callbar{left:636px;top:24px;display:flex;align-items:center;gap:10px;color:var(--white);font-family:'Open Sans',sans-serif;font-size:16px;font-weight:600}
.ring{width:32px;height:32px;border:2px solid var(--white);border-radius:50%;display:flex;align-items:center;justify-content:center}
.socials-top{left:910px;top:24px;display:flex;gap:6px}
.nav{left:497px;top:88px;display:flex;gap:38px;font-family:'Open Sans',sans-serif;font-size:17px;font-weight:600;color:var(--white)}
.hero-title{left:0;top:248px;width:1200px;text-align:center;color:var(--white);font-family:'Open Sans',sans-serif;font-weight:700;font-size:50px}
.hero-sub{left:0;top:335px;width:1200px;text-align:center;color:var(--white);font-family:'Open Sans',sans-serif;font-weight:600;font-size:31px}
.btn-outline{left:532px;top:418px;width:134px;height:49px;border:2px solid var(--white);color:var(--white);font-family:'Open Sans',sans-serif;font-size:17px;font-weight:600;display:flex;align-items:center;justify-content:center}
.hero-wave{left:0;top:460px;width:1200px;height:200px}

/* Section titles */
.sec-title{left:0;width:1200px;text-align:center;font-family:'Lato',sans-serif;font-weight:700;font-size:28px;color:var(--accent)}
.sec-rule{left:525px;width:150px;height:2px;background:var(--accent)}

/* Welcome */
.feature{width:190px;text-align:center}
.feature-badge{width:134px;height:134px;margin:0 auto;border:3px solid var(--navy);border-radius:50%;display:flex;align-items:center;justify-content:center}
.feature-badge span{width:114px;height:114px;border:2px solid var(--navy);border-radius:50%;background:radial-gradient(circle,#f1c36a 0 22%,#3d89c9 23% 45%,#fff 46%)}
.feature h3{margin-top:26px;font-family:'Roboto',sans-serif;font-weight:400;font-size:17px;color:var(--ink)}
.feature p{margin-top:18px;font-size:13px;line-height:21px;color:var(--muted)}

/* Services */
.services{left:0;top:1110px;width:1200px;height:453px;background:linear-gradient(135deg,#15588f,#0d4f86 60%,#0b4578)}
.services .sec-title{color:var(--white)}
.services .sec-rule{background:var(--white)}
.service{width:360px;color:var(--white)}
.service h3{font-family:'Roboto',sans-serif;font-weight:500;font-size:22px}
.service p{margin-top:16px;font-size:13px;line-height:23px}
.service-icon{width:74px;height:74px;background:rgba(255,255,255,.9);border-radius:50% 50% 8px 8px}

/* Blog */
.post-photo{width:197px;height:157px}
.post{width:280px}
.post h3{font-family:'Roboto',sans-serif;font-weight:400;font-size:18px}
.post time{display:block;margin-top:8px;font-size:12px;font-style:italic}
.post p{margin-top:12px;font-size:13px;line-height:21px;color:var(--muted)}
.post a{display:block;margin-top:14px;font-size:13px;font-weight:500;color:var(--navy);text-decoration:none}

/* Testimonials */
.testimonials{left:0;top:1915px;width:1200px;height:332px;background:var(--grey-band)}
.quote-mark{font-family:'Lato',sans-serif;font-weight:700;font-size:56px;color:var(--accent);line-height:1}
.quote-text{left:211px;top:2040px;width:776px;text-align:center;font-size:14px;line-height:27px;color:var(--ink)}
.socials-mid{left:475px;top:2156px;display:flex;gap:6px}
.socials-mid .ring{width:44px;height:44px;border-color:var(--ink)}

/* Footer */
.footer{left:0;top:2247px;width:1200px;height:334px;background:linear-gradient(150deg,#124f84,#0c4476)}
.foot-brand{left:99px;top:2391px}
.foot-head{font-family:'Open Sans',sans-serif;font-weight:700;font-size:17px;color:var(--white)}
.foot-head::after{content:"";display:block;width:100px;height:2px;background:var(--white);margin-top:10px}
.links{list-style:none;margin-top:20px;color:var(--white);font-size:14px}
.links li{margin-bottom:15px}
.links li::before{content:"› ";}
.contact-row{display:flex;gap:20px;margin-top:18px;color:var(--white);font-size:12px;line-height:20px}
.contact-row strong{font-size:14px;font-weight:500;display:block}
.contact-row .ring{width:34px;height:34px;flex:none}
.field{height:37px;border:1px solid var(--white);color:var(--white);font-size:11px;padding:10px 12px}
.send{left:812px;top:2463px;width:120px;height:39px;background:var(--accent-bright);color:var(--white);font-family:'Open Sans',sans-serif;font-size:12px;font-weight:600;display:flex;align-items:center;justify-content:center}

.legal{left:0;top:2581px;width:1200px;height:62px;background:var(--accent)}
.legal p{position:absolute;left:99px;top:21px;color:var(--white);font-size:13px}
.socials-foot{left:947px;top:2597px;display:flex;gap:6px}
.socials-foot .ring{width:32px;height:32px}
</style>
</head>
<body>

<header class="abs hero" role="img" aria-label="Photo of glass office towers viewed from below, blue tint"></header>
<div class="abs brand"><span class="brand-mark"></span>Quorvane</div>
<div class="abs callbar">
  <span class="ring"><svg width="14" height="14" viewBox="0 0 24 24" fill="#fff"><path d="M6.6 10.8a15 15 0 0 0 6.6 6.6l2.2-2.2c.3-.3.7-.4 1-.2 1.1.4 2.3.6 3.6.6.6 0 1 .4 1 1V20c0 .6-.4 1-1 1C10.6 21 3 13.4 3 4c0-.6.4-1 1-1h3.5c.6 0 1 .4 1 1 0 1.3.2 2.5.6 3.6.1.3 0 .7-.2 1z"/></svg></span>
  CALL US AT: 180 044 7719
</div>
<div class="abs socials-top"><span class="ring"></span><span class="ring"></span><span class="ring"></span><span class="ring"></span><span class="ring"></span></div>
<nav class="abs nav"><span>HOME</span><span>WHO WE ARE</span><span>OUR SOLUTIONS</span><span>NEWS</span><span>CONTACT</span></nav>
<h1 class="abs hero-title">QUORVANE SERVICES</h1>
<p class="abs hero-sub">See what outsourcing could do for your business</p>
<div class="abs btn-outline">READ MORE</div>
<svg class="abs hero-wave" viewBox="0 0 1200 200" preserveAspectRatio="none">
  <path d="M0,8 C300,150 750,200 1200,105 L1200,200 L0,200Z" fill="#1a8acb"/>
  <path d="M0,20 C280,150 720,205 1200,128 L1200,200 L0,200Z" fill="#fff"/>
</svg>

<h2 class="abs sec-title" style="top:708px">WELCOME TO QUORVANE</h2>
<div class="abs sec-rule" style="top:756px"></div>

<div class="abs feature" style="left:81px;top:810px"><div class="feature-badge" role="img" aria-label="Illustration of a customer service agent"><span></span></div><h3>Customer Service</h3><p>Sed ut perspiciatis unde omnis iste natus error sit voluptatem accusantium dolorem.</p></div>
<div class="abs feature" style="left:305px;top:810px"><div class="feature-badge" role="img" aria-label="Illustration of a shopping basket"><span></span></div><h3>Ecommerce</h3><p>Sed ut perspiciatis unde omnis iste natus error sit voluptatem accusantium dolorem.</p></div>
<div class="abs feature" style="left:508px;top:810px"><div class="feature-badge" role="img" aria-label="Illustration of a paint palette and brushes"><span></span></div><h3>Creative</h3><p>Sed ut perspiciatis unde omnis iste natus error sit voluptatem accusantium dolorem.</p></div>
<div class="abs feature" style="left:715px;top:810px"><div class="feature-badge" role="img" aria-label="Illustration of an IT professional"><span></span></div><h3>IT Solutions</h3><p>Sed ut perspiciatis unde omnis iste natus error sit voluptatem accusantium dolorem.</p></div>
<div class="abs feature" style="left:915px;top:810px"><div class="feature-badge" role="img" aria-label="Illustration of a group of staff"><span></span></div><h3>Human Resources</h3><p>Sed ut perspiciatis unde omnis iste natus error sit voluptatem accusantium dolorem.</p></div>

<section class="abs services" role="img" aria-label="Faded photo of an office meeting under a blue overlay"></section>
<h2 class="abs sec-title" style="top:1160px;color:#fff">QUORVANE SERVICES</h2>
<div class="abs sec-rule" style="top:1207px;background:#fff"></div>

<div class="abs service-icon" style="left:100px;top:1268px" role="img" aria-label="Icon of a business person"></div>
<div class="abs service" style="left:203px;top:1262px"><h3>BUSINESS PROCESS</h3><p>Sed ut perspiciatis unde omnis iste natus error sit vo luptatem accusantium doloremque laudantium totam rem aperiam, eaque ipsam.</p></div>
<div class="abs service-icon" style="left:662px;top:1268px" role="img" aria-label="Icon of a person with a currency sign"></div>
<div class="abs service" style="left:761px;top:1262px"><h3>BPO BUSINESS</h3><p>Sed ut perspiciatis unde omnis iste natus error sit vo luptatem accusantium doloremque laudantium totam rem aperiam, eaque ipsam.</p></div>
<div class="abs service-icon" style="left:100px;top:1405px;border-radius:6px" role="img" aria-label="Icon of office buildings"></div>
<div class="abs service" style="left:203px;top:1400px"><h3>OUTSOURCING COMPANY</h3><p>Sed ut perspiciatis unde omnis iste natus error sit vo luptatem accusantium doloremque laudantium totam rem aperiam, eaque ipsam.</p></div>
<div class="abs service-icon" style="left:662px;top:1405px;border-radius:6px" role="img" aria-label="Icon of a connected team structure"></div>
<div class="abs service" style="left:761px;top:1400px"><h3>QUORVANE PROCESS</h3><p>Sed ut perspiciatis unde omnis iste natus error sit vo luptatem accusantium doloremque laudantium totam rem aperiam, eaque ipsam.</p></div>

<h2 class="abs sec-title" style="top:1600px">OUR BLOG POSTS</h2>
<div class="abs sec-rule" style="top:1648px"></div>

<div class="abs post-photo" style="left:99px;top:1704px;background:linear-gradient(135deg,#8a7766,#4a4644 55%,#c9c2b8)" role="img" aria-label="Photo of colleagues working at desks in an office"></div>
<article class="abs post" style="left:314px;top:1704px"><h3>Business Process</h3><time>March 20, 2016</time><p>Sed ut perspiciatis unde omnis iste natus error sit voluptatem accusantium doloremque laudan-tium, totam rem aperiam.</p><a>Read More ➜</a></article>
<div class="abs post-photo" style="left:615px;top:1704px;background:linear-gradient(135deg,#1e3b52,#4d7a96 50%,#0e1f2e)" role="img" aria-label="Photo of a man looking at a digital display"></div>
<article class="abs post" style="left:830px;top:1704px"><h3>Outsourcing Company</h3><time>March 20, 2016</time><p>Sed ut perspiciatis unde omnis iste natus error sit voluptatem accusantium doloremque laudan-tium, totam rem aperiam.</p><a>Read More ➜</a></article>

<section class="abs testimonials"></section>
<h2 class="abs sec-title" style="top:1952px">OUR TESTIMONIALS</h2>
<div class="abs sec-rule" style="top:2000px"></div>
<div class="abs quote-mark" style="left:157px;top:2010px">“</div>
<p class="abs quote-text">Lorem ipsum dolor sit amet consectetur labore magna aliqua elit sed do eiusmod tempor incididunt ut labore et dolore magna aliqua veranesa at denim voluptatem accusantium doloremque laudantium, totam rem aperiam, eaque ipsa consec labore et dolore magna aliqua.</p>
<div class="abs quote-mark" style="left:1020px;top:2094px">”</div>
<div class="abs socials-mid"><span class="ring"></span><span class="ring"></span><span class="ring"></span><span class="ring"></span><span class="ring"></span></div>

<footer class="abs footer" role="img" aria-label="Faded photo of office towers under a blue overlay"></footer>
<div class="abs brand foot-brand"><span class="brand-mark"></span>Quorvane</div>
<div class="abs" style="left:384px;top:2286px">
  <div class="foot-head">QUICK LINKS</div>
  <ul class="links"><li>Home</li><li>About Us</li><li>Who We Are</li><li>Our Solutions</li><li>News</li><li>Contact Us</li></ul>
</div>
<div class="abs" style="left:560px;top:2286px;width:230px">
  <div class="foot-head">CONTACT US</div>
  <div class="contact-row" style="margin-top:22px"><span class="ring"><svg width="12" height="14" viewBox="0 0 12 16" fill="#fff"><path d="M6 0a6 6 0 0 0-6 6c0 4.5 6 10 6 10s6-5.5 6-10a6 6 0 0 0-6-6zm0 8.5A2.5 2.5 0 1 1 6 3.5a2.5 2.5 0 0 1 0 5z"/></svg></span><div><strong>QUORVANE,</strong>Larkmoor, Western Australia, 6094.</div></div>
  <div class="contact-row"><span class="ring"><svg width="10" height="14" viewBox="0 0 10 16"><rect x="1" y="1" width="8" height="14" rx="1.5" fill="none" stroke="#fff" stroke-width="1.6"/></svg></span><div><strong>PHONE:</strong>180 044 7719</div></div>
  <div class="contact-row"><span class="ring"><svg width="14" height="10" viewBox="0 0 16 12" fill="#fff"><path d="M0 0h16v1.5L8 7 0 1.5z M0 3.5l8 5.5 8-5.5V12H0z"/></svg></span><div><strong>Mail:</strong>info@quorvane.in</div></div>
</div>
<div class="abs" style="left:812px;top:2286px">
  <div class="foot-head">CONTACT FORM</div>
</div>
<div class="abs field" style="left:812px;top:2340px;width:139px">Name</div>
<div class="abs field" style="left:960px;top:2340px;width:141px">Phone</div>
<div class="abs field" style="left:812px;top:2384px;width:289px;height:65px">Message</div>
<div class="abs send">SEND MESSAGE</div>

<div class="abs legal"><p>Copyright © 2016 Quorvane. All Right Reserved</p></div>
<div class="abs socials-foot"><span class="ring"></span><span class="ring"></span><span class="ring"></span><span class="ring"></span></div>

</body>
</html>
```